UX - Need some screens design for a Skill Assessment Application

I am building an app to carry out skill assessments. Depending on how the assessment is configured, it may have one or more parts
1. Question based assessment (Multiple Choice, True False, Fill in the blanks"
2. Endorsement by two colleagues - A screen that allows user to pick colleagues based on search and shows the status of pending requests
3. A written submission - a page that explains the format of the submission and a file upload
As each assessment can be configured with or without any of the steps, the assessment UI must be such that these areas get hidden/displayed based on configuration.
Colour codes to be used can be #0e78bb and #ffffff
There will also be a start screen (instructions) and an end screen (results)
Target Market(s)
Enterprise software
Number of Pages Required
4 page

```html
<!DOCTYPE html>
<html lang="en">
<head>
<meta charset="utf-8">
<title>Skill Assessment – Quiz</title>
<link href="https://fonts.googleapis.com/css2?family=Inter:wght@400;500;600;700&display=swap" rel="stylesheet">
<style>
:root{
  --brand:#0e78bb;
  --header:#0457ad;
  --white:#ffffff;
  --ink:#1d1f24;
  --muted:#6b6f76;
  --faint:#a3a7ad;
  --line:#dfe2e6;
  --band:#f6f7f9;
  --chip:#e9ebee;
  --teal:#12939a;
  --track:#f1f3f5;
  --accent:#29a9e1;
}
*{box-sizing:border-box;margin:0;padding:0}
html,body{width:1200px;height:771px;overflow:hidden;background:var(--white);font-family:"Inter",sans-serif;color:var(--ink)}
.page{position:relative;width:1200px;height:771px}
.abs{position:absolute}
.topbar{left:0;top:0;width:1200px;height:43px;background:var(--header)}
.brand{left:71px;top:12px;display:flex;align-items:center;gap:8px;color:var(--white);font-size:14px;font-weight:600}
.brand-dot{width:16px;height:16px;border-radius:50%;background:var(--white)}
.nav{top:0;height:43px;font-size:12.5px;color:#cfe0f3;line-height:46px}
.nav.active{color:var(--white);font-weight:600;border-bottom:3px solid var(--accent);height:43px}
.avatar{left:1100px;top:8px;width:27px;height:27px;border-radius:50%;background:linear-gradient(135deg,#7a6a72,#3a3b55)}
.crumbs{left:88px;top:67px;font-size:11.5px;color:var(--muted)}
.crumbs a{color:var(--brand);text-decoration:none}
.title{left:122px;top:98px;font-size:21px;font-weight:600}
.updated{right:90px;top:111px;font-size:11px;color:var(--muted)}
.updated b{font-weight:500;color:#3b3e44}
.band{left:0;top:140px;width:1200px;height:45px;background:var(--band);border-top:1px solid var(--line);border-bottom:1px solid var(--line)}
.meta{top:155px;font-size:10.5px;color:var(--ink)}
.meta .v{color:var(--brand)}
.meta .g{color:var(--muted)}
.sep{top:154px;width:1px;height:15px;background:var(--line)}
.chip{top:151px;height:24px;border-radius:12px;background:var(--chip);font-size:11.5px;color:#555a60;font-weight:500;display:flex;align-items:center;justify-content:center}
.step{left:88px;width:214px;height:43px;border:1px solid var(--line);border-radius:3px;font-size:12.5px;color:var(--faint);padding-left:17px;display:flex;align-items:center}
.step.current{border:1.5px solid var(--brand);color:var(--ink)}
.section-title{left:366px;top:218px;font-size:16px;font-weight:700}
.btn{display:flex;align-items:center;justify-content:center;border-radius:3px;font-size:11.5px;font-weight:500}
.btn-outline{border:1px solid var(--brand);color:var(--brand);background:var(--white)}
.btn-solid{background:var(--brand);color:var(--white)}
.rule{left:366px;top:254px;width:744px;height:1px;background:var(--line)}
.qnum{left:366px;top:272px;font-size:15.5px;color:var(--muted)}
.qtext{left:412px;top:272px;font-size:15.5px;font-weight:500}
.pill{top:317px;height:30px;border-radius:15px;font-size:11.5px;font-weight:500;display:flex;align-items:center;justify-content:center}
.pill.on{background:var(--brand);color:var(--white)}
.pill.off{border:1px solid var(--line);color:var(--brand)}
.progress-label{left:908px;top:281px;font-size:12px;color:#3b3e44}
.count{left:1088px;top:282px;font-size:10px;color:var(--muted)}
.count b{color:#3b3e44}
.note{left:896px;top:325px;width:214px;height:128px;background:var(--band);border-radius:4px;padding:21px 20px}
.note h3{font-size:15px;font-weight:500;margin-bottom:12px}
.note p{font-size:11.5px;line-height:20.5px;color:var(--muted)}
.percent{left:88px;top:662px;font-size:27px;font-weight:700}
.percent small{font-size:13px;font-weight:600}
.track{left:0;top:701px;width:1200px;height:7px;background:var(--track)}
.fill{left:0;top:701px;width:465px;height:7px;background:var(--teal)}
.skip{left:998px;top:731px;font-size:11.5px;color:#3b3e44;display:flex;align-items:center;gap:4px}
</style>
</head>
<body>
<div class="page">
  <header class="abs topbar"></header>
  <div class="abs brand"><span class="brand-dot"></span>Orvanthe</div>
  <div class="abs nav active" style="left:487px">Assessments</div>
  <div class="abs nav" style="left:587px">Colleagues</div>
  <div class="abs nav" style="left:670px">Results</div>
  <svg class="abs" style="left:1027px;top:12px" width="18" height="19" viewBox="0 0 18 19" fill="none" stroke="#fff" stroke-width="1.3"><path d="M4 13V8a5 5 0 0 1 10 0v5l1.5 2h-13z"/><path d="M7.5 17.5h3"/></svg>
  <svg class="abs" style="left:1062px;top:13px" width="18" height="18" viewBox="0 0 24 24" fill="none" stroke="#fff" stroke-width="1.6"><circle cx="12" cy="12" r="3"/><path d="M12 2l2 3 3.5-1 .5 3.5 3 2-2 3 2 3-3 2-.5 3.5-3.5-1-2 3-2-3-3.5 1-.5-3.5-3-2 2-3-2-3 3-2L6.5 4 10 5z"/></svg>
  <div class="abs avatar" role="img" aria-label="User profile photo"></div>

  <svg class="abs" style="left:56px;top:65px" width="20" height="20" viewBox="0 0 20 20" fill="none" stroke="#0e78bb" stroke-width="1.6"><circle cx="10" cy="10" r="9"/><path d="M14 10H6M9.5 6.5L6 10l3.5 3.5"/></svg>
  <div class="abs crumbs"><a href="#">Assessment</a>&nbsp;&nbsp;/&nbsp;&nbsp;Application Design Capabilities</div>
  <svg class="abs" style="left:88px;top:101px" width="21" height="22" viewBox="0 0 21 22" fill="none" stroke="#555a60" stroke-width="1.4"><path d="M15 8V2H2v18h8"/><path d="M5 6h2M9 6h3M5 10h2M9 10h3M5 14h2"/><circle cx="15" cy="16" r="4"/><path d="M13.3 16l1.2 1.2 2.2-2.2M18 19l2 2"/></svg>
  <h1 class="abs title">Application Design Capabilities</h1>
  <div class="abs updated">Last Updated: <b>23/05/2024</b></div>

  <div class="abs band"></div>
  <div class="abs meta" style="left:88px">Assessment Date: <span class="v">May 20, 2024</span></div>
  <div class="abs sep" style="left:267px"></div>
  <div class="abs meta" style="left:288px">Assessment Type: <span class="v">UI/UX Skill</span></div>
  <div class="abs sep" style="left:451px"></div>
  <div class="abs meta" style="left:473px">Due Date: <span class="g">24/05/2024</span></div>
  <div class="abs chip" style="left:888px;width:41px">Quiz</div>
  <div class="abs chip" style="left:936px;width:88px">Endorsement</div>
  <div class="abs chip" style="left:1031px;width:79px">Submission</div>

  <div class="abs step current" style="top:219px">Quiz</div>
  <div class="abs step" style="top:271px">Endorsement</div>
  <div class="abs step" style="top:322px">Submission</div>

  <h2 class="abs section-title">Quiz</h2>
  <div class="abs btn btn-outline" style="left:1006px;top:213px;width:104px;height:31px">Save Progress</div>
  <div class="abs rule"></div>

  <div class="abs qnum">Q.7.</div>
  <div class="abs qtext">This is a single question with T/F choice</div>
  <div class="abs pill on" style="left:412px;width:52px">True</div>
  <div class="abs pill off" style="left:471px;width:55px">False</div>

  <svg class="abs" style="left:894px;top:283px" width="8" height="10" viewBox="0 0 8 10" fill="none" stroke="#3b3e44" stroke-width="1.3"><path d="M2 1l4 4-4 4"/></svg>
  <div class="abs progress-label">Progress</div>
  <svg class="abs" style="left:1050px;top:272px" width="31" height="31" viewBox="0 0 31 31" fill="none" stroke-width="3"><circle cx="15.5" cy="15.5" r="13" stroke="#e3e6ea"/><circle cx="15.5" cy="15.5" r="13" stroke="#29a9e1" stroke-dasharray="71.5 81.7" transform="rotate(-90 15.5 15.5)"/></svg>
  <div class="abs count"><b>7</b> / 8</div>

  <aside class="abs note">
    <h3>Note</h3>
    <p>Lorem ipsum dolor sit amet, consecteteur adispiscing elit. Lorem ipsum dolor sit amet</p>
  </aside>

  <div class="abs percent">35<small>%</small></div>
  <div class="abs track"></div>
  <div class="abs fill"></div>

  <div class="abs btn btn-outline" style="left:88px;top:722px;width:72px;height:31px">Go Back</div>
  <div class="abs skip">Skip <svg width="8" height="10" viewBox="0 0 8 10" fill="none" stroke="#3b3e44" stroke-width="1.3"><path d="M2 1l4 4-4 4"/></svg></div>
  <div class="abs btn btn-solid" style="left:1058px;top:722px;width:52px;height:31px">Next</div>
</div>
</body>
</html>
```